Stylish Business Cards Wanted

- DOUBLE SIDED Design Required -

High end, edgy cards for a corporate and personal stylist. Must include logo,
Name: Belinda Harwick
Title: Director and Stylist
telephone : +61 8 7142 5809
email: belinda@theloombriefing.example
website: theloombriefing.example
Tag: Corporate Workwear & Uniform Specialist | Personal Stylist
Would like nice icons for telephone, email, website

Target Market(s)

Businesses wanting stylish uniforms, people wanting stylish wardrobes

Industry/Entity Type

Corporate Workwear Stylist

Contact Information for Business Card

I would like black, white and gold foiling incorporated in the design - possibly a touch of the other colours on my branding guide attached Name: Belinda Harwick Title: Director and Stylist telephone : +61 8 7142 5809 email: belinda@theloombriefing.example website: theloombriefing.example Tag: Corporate Workwear & Uniform Specialist | Personal Stylist Would like nice icons for telephone, email, website

Font styles to use
Other font styles liked:
• Raleway

Colors

Designer to choose colors to be used in the design.

Requirements
Must have
• Gold foil accents

```html
<!DOCTYPE html>
<html lang="en">
<head>
<meta charset="utf-8">
<title>The Loom Briefing – Business Cards</title>
<link rel="stylesheet" href="https://fonts.googleapis.com/css2?family=Raleway:wght@500;700&family=Michroma&family=Arimo:wght@400&display=swap">
<style>
  :root {
    --backdrop: #2b2b2b;
    --card-white: #ffffff;
    --charcoal: #323132;
    --gold: #e4bd5d;
    --ink-light: #ffffff;
  }
  * { box-sizing: border-box; margin: 0; padding: 0; }
  html, body {
    width: 1200px; height: 880px; overflow: hidden;
    background: var(--backdrop);
  }
  .sheet {
    position: relative; width: 1200px; height: 880px;
    display: flex; flex-direction: column; align-items: center; justify-content: center;
    gap: 44px;
  }
  .card {
    position: relative; width: 640px; height: 366px;
    border-radius: 26px; overflow: hidden;
    background: var(--card-white);
  }
  .card-shape { position: absolute; inset: 0; }
  .brand {
    position: absolute; display: flex; align-items: center; gap: 10px;
    font-family: "Raleway", sans-serif; font-weight: 700;
    color: var(--charcoal); white-space: nowrap;
  }
  .brand-mark { width: 14px; height: 14px; background: var(--gold); flex: none; }
  .card--front .brand { left: 50%; top: 50%; transform: translate(-50%, -50%); font-size: 34px; }
  .card--back .brand { left: 30px; top: 160px; font-size: 24px; }

  .tagline {
    position: absolute; left: 30px; top: 198px; width: 270px;
    font-family: "Raleway", sans-serif; font-weight: 500; font-size: 10px;
    line-height: 1.5; letter-spacing: 0.3px; color: var(--charcoal);
  }

  .holder {
    position: absolute; left: 360px; top: 38px; color: var(--ink-light);
  }
  .holder-name {
    font-family: "Michroma", sans-serif; font-size: 15px; letter-spacing: 2.5px;
  }
  .holder-title {
    font-family: "Raleway", sans-serif; font-weight: 500; font-size: 9px; margin-top: 3px;
  }
  .address {
    position: absolute; right: 26px; top: 98px; text-align: right;
    font-family: "Arimo", sans-serif; font-size: 13px; line-height: 1.3; color: var(--ink-light);
  }
  .contact-list {
    position: absolute; left: 392px; top: 168px; list-style: none;
    font-family: "Arimo", sans-serif; font-size: 12.5px; color: var(--ink-light);
  }
  .contact-list li { display: flex; align-items: center; gap: 10px; height: 34px; }
  .contact-icon { width: 16px; height: 16px; flex: none; }
</style>
</head>
<body>
<main class="sheet">
  <section class="card card--front" aria-label="Card front">
    <div class="brand"><span class="brand-mark"></span>The Loom Briefing</div>
  </section>

  <section class="card card--back" aria-label="Card back">
    <svg class="card-shape" viewBox="0 0 640 366" aria-hidden="true">
      <rect width="640" height="366" fill="var(--charcoal)"/>
      <path d="M0 0 H250 C340 30 390 170 365 366 H0 Z" fill="var(--card-white)"/>
      <path d="M300 70 C365 140 372 260 335 366 H350 C382 260 374 140 300 70 Z" fill="var(--gold)"/>
    </svg>

    <div class="brand"><span class="brand-mark"></span>The Loom Briefing</div>
    <p class="tagline">Corporate Workwear &amp; Uniform Specialist<br>Personal Stylist</p>

    <div class="holder">
      <p class="holder-name">BELINDA HARWICK</p>
      <p class="holder-title">Director and Stylist</p>
    </div>

    <p class="address">14 Wattle Lane Norwood,<br>SA, AU</p>

    <ul class="contact-list">
      <li>
        <svg class="contact-icon" viewBox="0 0 16 16" aria-hidden="true"><path d="M3 1.5 L5.5 1 L7 4.5 L5.3 5.8 C6 7.6 8.2 9.9 10.2 10.7 L11.5 9 L15 10.5 L14.5 13 C14.3 14 13.4 14.6 12.4 14.5 C6.5 13.8 2.2 9.5 1.5 3.6 C1.4 2.6 2 1.7 3 1.5 Z" fill="var(--ink-light)"/></svg>
        <span>+61 8 7142 5809</span>
      </li>
      <li>
        <svg class="contact-icon" viewBox="0 0 16 16" aria-hidden="true"><rect x="4" y="1" width="8" height="14" rx="1.5" fill="none" stroke="var(--ink-light)" stroke-width="1.4"/><circle cx="8" cy="12.6" r="0.9" fill="var(--ink-light)"/></svg>
        <span>+61 8 7142 5810</span>
      </li>
      <li>
        <svg class="contact-icon" viewBox="0 0 16 16" aria-hidden="true"><rect x="1" y="3.5" width="14" height="9.5" fill="none" stroke="var(--ink-light)" stroke-width="1.3"/><path d="M1 3.5 L8 9 L15 3.5" fill="none" stroke="var(--ink-light)" stroke-width="1.3"/></svg>
        <span>belinda@theloombriefing.example</span>
      </li>
      <li>
        <svg class="contact-icon" viewBox="0 0 16 16" aria-hidden="true"><g fill="none" stroke="var(--ink-light)" stroke-width="1.2"><circle cx="8" cy="8" r="6.6"/><ellipse cx="8" cy="8" rx="3" ry="6.6"/><path d="M1.4 8 H14.6 M2.5 4.6 H13.5 M2.5 11.4 H13.5"/></g></svg>
        <span>theloombriefing.example</span>
      </li>
    </ul>
  </section>
</main>
</body>
</html>
```